New Business Card for Web Design/Internet Marketing Company

Looking for a great looking new business card. We are a 10 year old web design, internet marketing and website management company that works mostly with small businesses.

Our new card needs to better match the colors and style of our website, be bold, extremely usable and slightly edgy.

Target Market(s)

Small/Medium businesses that have websites

Industry/Entity Type

Internet

Requirements
Must have
• Front and back design, full color, rounded corners please

Must use the colors/style of our website (JPG provided)

INFO FOR CARDS (as readable as possible please)
Mark Lenner
President/CEO
mark@trelvanmedia.example
Phone: 520-381-7459
Toll Free: 866-381-7459
Address: 4315 W. Calloway Ave. Ste. 140, Tucson, AZ 85792

THINGS I WANT TO PROMOTE (if there is room):
1. Our Website - www.trelvanmedia.example

2. Social Media
Twitter: @trelvanmedia
Facebook: www.facebook.com/trelvanmedia

3. Our Services
Web Design
Internet Marketing
Website Management

```html
<!DOCTYPE html>
<html lang="en">
<head>
<meta charset="utf-8">
<title>Trelvan Media – Business Card, Front and Back</title>
<link rel="stylesheet" href="https://fonts.googleapis.com/css2?family=Cabin:ital,wght@0,400;0,600;0,700;1,400&display=swap">
<style>
  :root {
    --page: #ffffff;
    --card-navy: #07078a;
    --accent-orange: #f27b1f;
    --accent-cyan: #1bb8c6;
    --watermark: #1a2fa0;
    --card-shadow: rgba(0, 0, 0, 0.35);
  }
  * { box-sizing: border-box; margin: 0; padding: 0; }
  html, body {
    width: 1200px;
    height: 1200px;
    overflow: hidden;
    background: var(--page);
    font-family: "Cabin", "Trebuchet MS", sans-serif;
  }
  .sheet {
    position: relative;
    width: 1200px;
    height: 1200px;
  }
  .card {
    position: absolute;
    left: 100px;
    width: 1000px;
    height: 540px;
    background: var(--card-navy);
    border-radius: 22px;
    box-shadow: 4px 6px 10px var(--card-shadow);
    color: var(--accent-orange);
    overflow: hidden;
  }
  .card--front { top: 40px; }
  .card--back { top: 620px; }

  /* Brand mark: name plus one plain circle */
  .brand {
    display: flex;
    align-items: center;
    gap: 18px;
    color: var(--accent-orange);
    font-weight: 700;
    white-space: nowrap;
  }
  .brand__dot {
    flex: none;
    border-radius: 50%;
    background: var(--accent-cyan);
  }

  /* Front */
  .front__url {
    position: absolute;
    top: 30px;
    left: 36px;
    font-size: 22px;
    letter-spacing: 0.5px;
  }
  .front__brand {
    position: absolute;
    top: 170px;
    left: 0;
    right: 0;
    justify-content: center;
    font-size: 76px;
  }
  .front__brand .brand__dot { width: 70px; height: 70px; }
  .front__services {
    position: absolute;
    left: 60px;
    bottom: 34px;
    list-style: none;
    font-style: italic;
    font-size: 24px;
    line-height: 1.2;
  }
  .front__social {
    position: absolute;
    right: 40px;
    bottom: 120px;
    font-style: italic;
    font-size: 24px;
    line-height: 1.3;
  }
  .front__social dt { display: inline; }
  .front__social dd { display: inline; margin-left: 8px; }
  .front__social div { text-align: left; }

  /* Back */
  .back__brand {
    position: absolute;
    top: 70px;
    left: 30px;
    font-size: 40px;
    gap: 12px;
  }
  .back__brand .brand__dot { width: 40px; height: 40px; }
  .back__watermark {
    position: absolute;
    top: 190px;
    left: 220px;
    color: var(--watermark);
    font-size: 96px;
    font-weight: 700;
    white-space: nowrap;
    opacity: 0.8;
  }
  .back__person {
    position: absolute;
    top: 36px;
    right: 60px;
    font-size: 23px;
    line-height: 1.25;
  }
  .back__person .person__name { font-weight: 700; }
  .back__rule {
    position: absolute;
    left: 0;
    right: 0;
    bottom: 78px;
    height: 14px;
    background: var(--accent-orange);
  }
  .back__contact {
    position: absolute;
    left: 30px;
    right: 20px;
    bottom: 30px;
    font-size: 21px;
    white-space: nowrap;
  }
</style>
</head>
<body>
<main class="sheet">

  <section class="card card--front" aria-label="Card front">
    <p class="front__url">www.trelvanmedia.example</p>

    <div class="brand front__brand">
      <span class="brand__dot"></span>
      <span class="brand__name">Trelvan Media</span>
    </div>

    <dl class="front__social">
      <div><dt>Twitter:</dt><dd>@trelvanmedia</dd></div>
      <div><dt>Facebook:</dt><dd>www.facebook.com/trelvanmedia</dd></div>
    </dl>

    <ul class="front__services">
      <li>Web Design</li>
      <li>Website Management</li>
      <li>Internet Marketing</li>
    </ul>
  </section>

  <section class="card card--back" aria-label="Card back">
    <div class="back__watermark" aria-hidden="true">Trelvan Media</div>

    <div class="brand back__brand">
      <span class="brand__dot"></span>
      <span class="brand__name">Trelvan Media</span>
    </div>

    <div class="back__person">
      <p class="person__name">Mark Lenner</p>
      <p class="person__title">President/CEO</p>
      <p class="person__email">mark@trelvanmedia.example</p>
    </div>

    <div class="back__rule"></div>
    <p class="back__contact">Phone: 520-381-7459, Toll Free: 866-381-7459, Address: 4315 W. Calloway Ave. Ste. 140, Tucson, AZ 85792</p>
  </section>

</main>
</body>
</html>
```